Redesign current business card for food company

i would like to redesign my business card. our company is food company, our product range from chips, juices, milk and etc (mostly dried food stuff).
I want o keep same logo but , the rest is open to new design.
you can check at our website about our company www.orvelpantry.com

Target Market(s)

most of food company

Industry/Entity Type

Business

Contact Information for Business Card

I want to keep more to blue color...

Colors
3176b5
abd036

Requirements
Must have
• our old logo
Nice to have
• we do not mind to have nice material on bus card in order to accomplish nice design. for example: using spot uv, embossed and etc.

```html
<!DOCTYPE html>
<html lang="en">
<head>
<meta charset="utf-8">
<title>Orvel Pantry – Business Card</title>
<link rel="stylesheet" href="https://fonts.googleapis.com/css2?family=Montserrat:wght@400;500;700&display=swap">
<style>
  :root {
    --page-bg: #eceef3;
    --card-white: #ffffff;
    --brand-violet: #4b50b8;
    --brand-violet-soft: #6d70c9;
    --brand-indigo: #24238f;
    --brand-cyan: #1fb0c6;
    --text-violet: #3a3ea6;
    --back-top: #6266cb;
    --back-bottom: #1c1b86;
    --shadow: rgba(20, 22, 60, 0.18);
  }
  * { box-sizing: border-box; margin: 0; padding: 0; }
  html, body {
    width: 1200px; height: 913px; overflow: hidden;
    background: var(--page-bg);
    font-family: "Montserrat", sans-serif;
  }
  .canvas {
    width: 1200px; height: 913px;
    display: flex; align-items: center; justify-content: center; gap: 44px;
  }
  .card {
    position: relative;
    width: 520px; height: 297px;
    border-radius: 16px;
    overflow: hidden;
    box-shadow: 0 14px 30px var(--shadow);
  }
  .card-front { background: var(--card-white); }
  .card-front .bands { position: absolute; inset: 0; width: 100%; height: 100%; }
  .wordmark {
    position: absolute; left: 52px; top: 112px;
    font-weight: 700; font-size: 62px; letter-spacing: -1px;
    color: var(--brand-violet);
  }
  .contact {
    position: absolute; left: 292px; top: 62px;
    color: var(--text-violet);
    font-size: 11.5px; line-height: 1.45;
  }
  .contact .name { font-weight: 700; font-size: 16px; line-height: 1.2; }
  .contact .role { color: var(--brand-cyan); font-size: 12px; margin-bottom: 6px; }
  .contact .address { margin-bottom: 6px; }
  .contact ul { list-style: none; }
  .contact li { display: flex; align-items: center; gap: 7px; }
  .contact li svg { width: 11px; height: 11px; flex: none; fill: var(--text-violet); }

  .card-back {
    background: linear-gradient(155deg, var(--back-top) 0%, var(--brand-violet) 45%, var(--back-bottom) 100%);
  }
  .back-mark {
    position: absolute; left: 150px; top: 78px;
    font-weight: 700; font-size: 96px; letter-spacing: -2px;
    color: rgba(255, 255, 255, 0.12);
  }
  .back-url {
    position: absolute; right: 52px; bottom: 44px;
    color: #ffffff; font-size: 15px; letter-spacing: 0.5px;
  }
</style>
</head>
<body>
<main class="canvas">
  <section class="card card-front" aria-label="Business card front">
    <svg class="bands" viewBox="0 0 520 297" preserveAspectRatio="none" aria-hidden="true">
      <polygon points="300,0 520,0 520,30 250,30" fill="var(--brand-violet-soft)"/>
      <line x1="0" y1="33" x2="520" y2="33" stroke="var(--brand-cyan)" stroke-width="2"/>
      <line x1="0" y1="264" x2="520" y2="264" stroke="var(--brand-cyan)" stroke-width="2"/>
      <polygon points="0,267 370,267 330,297 0,297" fill="var(--brand-violet)"/>
    </svg>

    <div class="wordmark">orvel</div>

    <div class="contact">
      <p class="name">Daniel Harsono</p>
      <p class="role">President</p>
      <p class="address">Orvel Enterprises Corp.<br>2418 W 5th St.<br>Ontario CA 91762</p>
      <ul>
        <li><svg viewBox="0 0 24 24"><path d="M6.6 10.8a15.1 15.1 0 0 0 6.6 6.6l2.2-2.2c.3-.3.7-.4 1-.2 1.1.4 2.3.6 3.6.6.6 0 1 .4 1 1V20c0 .6-.4 1-1 1C10.6 21 3 13.4 3 4c0-.6.4-1 1-1h3.5c.6 0 1 .4 1 1 0 1.3.2 2.5.6 3.6.1.3 0 .7-.2 1z"/></svg>909 555 0142</li>
        <li><svg viewBox="0 0 24 24"><path d="M6 3h10v5H6zM4 9h16a2 2 0 0 1 2 2v6h-4v4H6v-4H2v-6a2 2 0 0 1 2-2zm4 7v3h8v-3z"/></svg>909 555 0143</li>
        <li><svg viewBox="0 0 24 24"><path d="M7 1h10a2 2 0 0 1 2 2v18a2 2 0 0 1-2 2H7a2 2 0 0 1-2-2V3a2 2 0 0 1 2-2zm0 3v14h10V4zm5 15.5a1 1 0 1 0 0 2 1 1 0 0 0 0-2z"/></svg>626 555 0187</li>
        <li><svg viewBox="0 0 24 24"><path d="M2 5h20v14H2zm2 2v.5l8 5 8-5V7zm0 2.8V17h16V9.8l-8 5z"/></svg>daniel@orvelpantry.com</li>
        <li><svg viewBox="0 0 24 24"><path d="M12 2a10 10 0 1 0 0 20 10 10 0 0 0 0-20zm6.9 9h-3a15 15 0 0 0-1.3-5.6A8 8 0 0 1 18.9 11zM12 4c.9 1.2 1.8 3.6 1.9 7h-3.8C10.2 7.6 11.1 5.2 12 4zM9.4 5.4A15 15 0 0 0 8.1 11h-3a8 8 0 0 1 4.3-5.6zM5.1 13h3a15 15 0 0 0 1.3 5.6A8 8 0 0 1 5.1 13zm6.9 7c-.9-1.2-1.8-3.6-1.9-7h3.8c-.1 3.4-1 5.8-1.9 7zm2.6-1.4a15 15 0 0 0 1.3-5.6h3a8 8 0 0 1-4.3 5.6z"/></svg>www.orvelpantry.com</li>
      </ul>
    </div>
  </section>

  <section class="card card-back" aria-label="Business card back">
    <div class="back-mark">orvel</div>
    <p class="back-url">www.orvelpantry.com</p>
  </section>
</main>
</body>
</html>
```